Computer consultant business card

Bexil Software is a newly started computer consulting company. It's a small one-man company that provides mostly Vornix applications but also websites in collaboration with designers. I'm running this company on the side of full time university studies.

I want the final design to be clean and memorable. Be creative! :)

Some inspiration:
http://www.pixelmarta.com/design/48317
http://www.pixelmarta.com/design/2739164/business-card-design-by-frostlynk
http://www.pixelmarta.com/design/604281/business-card-design-by-koralind-vestrabanu

See attachment for my company logo.
Updates

I would like to thank everyone for submitting! I'll need a couple of days to review and ultimately select a design.

Target Market(s)

Non-technical entrepreneurs and small companies.

Industry/Entity Type

University

Requirements
Must have
• My company logo.
In any way, both colors from my logo.
First- and last name, e-mail and phone number.
Double-sided design.
Nice to have
• Something creative with the symbol in my logo

```html
<!DOCTYPE html>
<html lang="en">
<head>
<meta charset="utf-8">
<title>Bexil Software – Business Card</title>
<link href="https://fonts.googleapis.com/css2?family=Arimo:wght@400;700&display=swap" rel="stylesheet">
<style>
  :root {
    --backdrop: #e6e2dd;
    --card-light: #ffffff;
    --card-shade: #ececec;
    --card-edge: #5a5a5a;
    --ink: #333333;
    --ink-soft: #3d3d3d;
    --brand-blue: #4671b8;
  }
  * { margin: 0; padding: 0; box-sizing: border-box; }
  html, body {
    width: 1200px;
    height: 1040px;
    overflow: hidden;
    background: var(--backdrop);
    font-family: "Arimo", Arial, sans-serif;
  }
  .canvas {
    position: relative;
    width: 1200px;
    height: 1040px;
  }
  .card {
    position: absolute;
    top: 60px;
    width: 521px;
    height: 910px;
    border: 1px solid var(--card-edge);
    background: radial-gradient(ellipse at 50% 50%, var(--card-light) 0%, var(--card-light) 35%, var(--card-shade) 100%);
    overflow: hidden;
    text-align: center;
    color: var(--ink);
  }
  .card--front { left: 54px; }
  .card--back  { left: 619px; }

  .wordmark {
    position: absolute;
    left: 0;
    width: 100%;
    display: flex;
    align-items: center;
    justify-content: center;
    color: var(--ink);
    font-weight: 700;
    white-space: nowrap;
  }
  .wordmark__dot {
    display: inline-block;
    flex: none;
    background: var(--brand-blue);
  }
  .card--front .wordmark {
    top: 116px;
    gap: 24px;
    font-size: 100px;
    line-height: 1;
    letter-spacing: -1px;
  }
  .card--front .wordmark__dot { width: 70px; height: 70px; }

  .person {
    position: absolute;
    top: 370px;
    left: 0;
    width: 100%;
  }
  .person__first {
    color: var(--brand-blue);
    font-weight: 700;
    font-size: 38px;
    line-height: 42px;
  }
  .person__last {
    color: var(--ink);
    font-size: 30px;
    line-height: 38px;
  }

  .contact {
    position: absolute;
    top: 514px;
    left: 0;
    width: 100%;
    font-size: 31px;
    line-height: 47px;
    color: var(--ink-soft);
    white-space: nowrap;
  }
  .contact__label {
    color: var(--brand-blue);
    font-weight: 700;
  }

  .address {
    position: absolute;
    top: 645px;
    left: 0;
    width: 100%;
    font-size: 31px;
    line-height: 47px;
    color: var(--ink-soft);
    white-space: nowrap;
  }

  .card--back .wordmark {
    top: 390px;
    gap: 28px;
    font-size: 124px;
    line-height: 1;
    letter-spacing: -2px;
  }
  .card--back .wordmark__dot {
    width: 90px;
    height: 90px;
    border-radius: 50%;
  }
</style>
</head>
<body>
<main class="canvas">

  <section class="card card--front" aria-label="Business card front">
    <div class="wordmark">
      <span class="wordmark__dot" aria-hidden="true"></span>
      <span class="wordmark__name">Bexil</span>
    </div>

    <div class="person">
      <p class="person__first">First Name</p>
      <p class="person__last">Last Name</p>
    </div>

    <div class="contact">
      <p><span class="contact__label">P :</span> 555-019-4826</p>
      <p><span class="contact__label">E :</span> hello@bexilsoft-studio.net</p>
    </div>

    <div class="address">
      <p>Street Name, City Name</p>
      <p>State, City Zip Code</p>
    </div>
  </section>

  <section class="card card--back" aria-label="Business card back">
    <div class="wordmark">
      <span class="wordmark__dot" aria-hidden="true"></span>
      <span class="wordmark__name">Bexil</span>
    </div>
  </section>

</main>
</body>
</html>
```